Income Tax and Accounting Brochure

I need a brochure using my new logo (file attached). I do tax work and accounting work. I am an EA (QFB Enrolled Agent - logo attached) and would like this incorporated into the brochure. I also have a MSA in Accounting. Please incorporate the text that I have provided in the brochure.
Updates

Need extra days to review

Target Market(s)

Tax Clients - both business and individuals

Industry/Entity Type

Accounting

Colors
0054AA
0677BA
7BADD7
CADEEF
E8F1F8

Requirements
Must have
• Use my logo and the QFB EA file in the brochure
Nice to have
• I would like to see a brochure that I can customize with my own text if possible.

```html
<!DOCTYPE html>
<html lang="en">
<head>
<meta charset="utf-8">
<title>Northfield Accounting &amp; Consulting – Brochure</title>
<link href="https://fonts.googleapis.com/css2?family=Rubik:ital,wght@0,400;0,500;0,600;0,700;1,400&display=swap" rel="stylesheet">
<style>
  :root{
    --navy:#0054AA;
    --blue:#0677BA;
    --sky:#7BADD7;
    --ice:#CADEEF;
    --mist:#E8F1F8;
    --red:#B5092E;
    --magenta:#CF1558;
    --ink:#2b2b2b;
    --stage:#b9bcc0;
    --white:#ffffff;
  }
  *{box-sizing:border-box;margin:0;padding:0}
  html,body{width:1200px;height:851px;overflow:hidden}
  body{background:var(--stage);font-family:"Rubik",sans-serif;color:var(--ink);position:relative}
  .page{position:absolute;top:108px;width:453px;height:640px;background:var(--white);overflow:hidden}
  .page--front{left:129px}
  .page--back{left:637px}
  .abs{position:absolute}

  /* brand lockup */
  .brand{display:flex;align-items:center;gap:6px}
  .brand__dot{border-radius:50%;background:var(--navy);flex:none}
  .brand__name{color:var(--navy);font-weight:500;line-height:1.15;letter-spacing:.3px}

  /* front */
  .hero{left:0;top:0}
  .front-brand{left:238px;top:42px}
  .front-brand .brand__dot{width:44px;height:44px}
  .front-brand .brand__name{font-size:12.5px}
  .portrait{left:256px;top:145px;width:148px;height:148px;border-radius:50%;background:radial-gradient(circle at 50% 45%,#a07860 0%,#5a4438 45%,#1c1c1e 75%);border:3px solid var(--white);box-shadow:0 2px 6px rgba(0,0,0,.25)}
  .principal{left:200px;top:313px;width:242px;text-align:center}
  .principal__name{color:var(--navy);font-weight:600;font-size:16px}
  .principal__role{color:var(--red);font-style:italic;font-size:15px;margin-top:2px}

  .bar{position:absolute;height:21px;display:flex;align-items:center;color:var(--white);font-weight:600;font-size:12.5px}
  .bar__dot{position:absolute;left:-2px;top:-1px;width:23px;height:23px;border-radius:50%;background:var(--white);border:3px solid var(--navy)}
  .bar__label{padding-left:28px}
  .bar--about{left:44px;top:382px;width:368px;background:var(--red)}
  .bar--about .bar__label{padding-left:37px}

  .about{left:37px;top:419px;width:376px;font-size:11px;line-height:13.2px;text-align:justify}
  .about p+p{margin-top:13px}
  .front-cta{left:37px;top:555px;width:376px;text-align:center}
  .front-cta__phone{color:var(--navy);font-weight:600;font-size:27px;line-height:30px}
  .front-cta__web{color:var(--red);font-weight:700;font-size:24px;line-height:28px}

  /* back */
  .bar--pink{left:42px;width:369px;background:linear-gradient(90deg,var(--magenta),#c4124e)}
  .bar--pink .bar__label{padding-left:29px}
  .bar--joy{top:39px}
  .bar--get{top:195px}
  .bar--books{top:378px}
  .copy{left:42px;width:369px;font-size:8.6px;line-height:11.4px;text-align:justify}
  .copy__title{color:var(--navy);font-weight:500;font-size:8.8px;margin-bottom:2px}
  .copy p+p{margin-top:11px}
  .copy--tax{top:69px}
  .copy--books{top:407px}
  .checks{position:absolute;left:42px;top:229px;width:369px;list-style:none;font-size:8.6px;line-height:11.4px;text-align:justify}
  .checks::before{content:"";position:absolute;left:4.5px;top:6px;bottom:4px;border-left:1px solid var(--sky)}
  .checks li{position:relative;padding-left:14px;margin-bottom:11.5px}
  .checks svg{position:absolute;left:0;top:1px}

  .footer-wave{left:0;top:440px}
  .back-brand{left:34px;top:482px}
  .back-brand .brand__dot{width:46px;height:46px}
  .back-brand .brand__name{font-size:13px}
  .back-cta{right:16px;top:510px;text-align:right;color:var(--white)}
  .back-cta__head{font-weight:600;font-size:21px;line-height:24px}
  .back-cta__phone{font-weight:600;font-size:21px;line-height:25px}
  .back-cta__web{font-weight:600;font-size:12.5px;line-height:15px}
  .back-cta__addr{font-size:14px;line-height:17px;margin-top:10px;padding-right:7px}
</style>
</head>
<body>

<section class="page page--front">
  <svg class="abs hero" width="453" height="360" viewBox="0 0 453 360">
    <defs>
      <linearGradient id="heroTone" x1="0" y1="0" x2="1" y2="1">
        <stop offset="0" stop-color="#d9c4b3"/>
        <stop offset=".45" stop-color="#e8743f"/>
        <stop offset="1" stop-color="#e9e4de"/>
      </linearGradient>
    </defs>
    <path role="img" aria-label="Photo of a delighted woman cheering at her laptop" fill="url(#heroTone)" d="M0,0 H453 V118 C330,150 230,330 110,348 C60,352 20,320 0,288 Z"/>
    <path fill="none" stroke="var(--red)" stroke-width="4" d="M453,120 C330,152 230,332 110,350 C60,354 20,322 0,290"/>
    <path fill="none" stroke="var(--navy)" stroke-width="6" d="M270,210 C220,270 170,340 110,355 C60,360 20,330 0,296"/>
  </svg>

  <div class="abs brand front-brand">
    <span class="brand__dot"></span>
    <span class="brand__name">NORTHFIELD ACCOUNTING<br>&amp; CONSULTING, LLC</span>
  </div>

  <div class="abs portrait" role="img" aria-label="Portrait photo of the principal"></div>

  <div class="abs principal">
    <div class="principal__name">Marian T Holloway, MSA EA</div>
    <div class="principal__role">(Principal)</div>
  </div>

  <div class="bar bar--about"><span class="bar__dot"></span><span class="bar__label">ABOUT</span></div>

  <div class="abs about">
    <p>I have a Masters' Degree in accounting &amp; am an QFB Enrolled Agent. I am also a LedgerPro Advanced Certified Consultant in both the online &amp; desktop products including Enterprise &amp; Point of Sale. I provide individual &amp; small business tax services, Accounting, bookkeeping, QFB representation, insurance audit representation, business license assistance &amp; more.</p>
    <p>I have experience working with a wide variety of clients from the point where they first decide they want to start a business. They are often unsure about what to do first- I have a lot of experience to offer you.</p>
  </div>

  <div class="abs front-cta">
    <div class="front-cta__phone">Call Us Today (555)214-0387</div>
    <div class="front-cta__web">WWW.NORTHFIELDTAX.COM</div>
  </div>
</section>

<section class="page page--back">
  <div class="bar bar--pink bar--joy"><span class="bar__dot"></span><span class="bar__label">What a joy it is to watch success in action!</span></div>

  <div class="abs copy copy--tax">
    <div class="copy__title">Tax Preparation – why hire us?</div>
    <p>Preparing your own income tax return can be a task that leaves you with more questions than answers. According to a study released by the national Public Accounting Office last year, most taxpayers (77% of 71 million taxpayers) believe they benefited from using a professional tax preparer.</p>
    <p>Whether we like it or not, today's tax laws are so complicated that filing a relatively simple return can be confusing. It is just too easy to overlook deductions and credits to which you are entitled. Even if you use a computer software program there's no substitute for the assistance of an experienced tax professional.</p>
  </div>

  <div class="bar bar--pink bar--get"><span class="bar__dot"></span><span class="bar__label">Here's what your get...</span></div>

  <ul class="checks">
    <li><svg width="10" height="10" viewBox="0 0 10 10"><circle cx="5" cy="5" r="5" fill="var(--blue)"/><path d="M2.6 5.1 4.3 6.7 7.4 3.5" fill="none" stroke="#fff" stroke-width="1.3"/></svg>Your tax return will be checked and rechecked by our computer software identifying potential problems the QFB may look at more closely and reviewing the math to limit QFB contacts.</li>
    <li><svg width="10" height="10" viewBox="0 0 10 10"><circle cx="5" cy="5" r="5" fill="var(--blue)"/><path d="M2.6 5.1 4.3 6.7 7.4 3.5" fill="none" stroke="#fff" stroke-width="1.3"/></svg>Your tax return can be filed electronically so you will get a refund back quicker.</li>
    <li><svg width="10" height="10" viewBox="0 0 10 10"><circle cx="5" cy="5" r="5" fill="var(--blue)"/><path d="M2.6 5.1 4.3 6.7 7.4 3.5" fill="none" stroke="#fff" stroke-width="1.3"/></svg>Our staff will show you how to adjust your payroll withholding to get more money back each week. Why give the QFB an interest free loan for up to 16 months.</li>
    <li><svg width="10" height="10" viewBox="0 0 10 10"><circle cx="5" cy="5" r="5" fill="var(--blue)"/><path d="M2.6 5.1 4.3 6.7 7.4 3.5" fill="none" stroke="#fff" stroke-width="1.3"/></svg>We will show you potential deductions to limit your tax liability for next year. In addition, we will give you a sheet of commonly overlooked deductions to limit the following year's tax liability.</li>
  </ul>

  <div class="bar bar--pink bar--books"><span class="bar__dot"></span><span class="bar__label">Books a Mess: No Problem!</span></div>

  <div class="abs copy copy--books">
    <p>If you own a small business and haven't kept up your bookkeeping, don't worry. We can help you. We'll prepare your bookkeeping for the year, prepare a full Schedule C, as well as your personal income tax return. Then we'll help you set up an easy system that allows you to keep your books in tip-top shape next year.</p>
  </div>

  <svg class="abs footer-wave" width="453" height="200" viewBox="0 0 453 200">
    <defs>
      <linearGradient id="footBlue" x1="0" y1="1" x2="1" y2="0">
        <stop offset="0" stop-color="var(--navy)"/>
        <stop offset="1" stop-color="var(--blue)"/>
      </linearGradient>
    </defs>
    <path fill="url(#footBlue)" d="M0,108 C30,150 70,165 110,160 C220,140 330,20 453,6 V200 H0 Z"/>
    <path fill="none" stroke="var(--red)" stroke-width="3" d="M0,100 C30,142 70,158 110,153 C220,132 330,12 453,-1"/>
    <path fill="none" stroke="var(--ice)" stroke-width="1.5" d="M0,95 C30,137 70,153 110,148 C220,127 330,7 453,-6"/>
  </svg>

  <div class="abs brand back-brand">
    <span class="brand__dot"></span>
    <span class="brand__name">NORTHFIELD ACCOUNTING<br>&amp; CONSULTING, LLC</span>
  </div>

  <div class="abs back-cta">
    <div class="back-cta__head">Call Us</div>
    <div class="back-cta__phone">(555)214-0387</div>
    <div class="back-cta__web">NORTHFIELDTAX.COM</div>
    <div class="back-cta__addr">2870 Orchard Hill Rd<br>PO Box 14, Linwood, VA 20000</div>
  </div>
</section>

</body>
</html>
```